New Business Card for Software Company

We are looking at rebranding a 10 year old company that specializes in PDF and DWF solutions for Architects and Engineers. We will attach the new company logo that we are going with so you can work with that and complimentary colors.
The sample information we would like on the business card is:
Gerald Pinfold
Vice President
4738 W. Harrowgate Lane. STE 305
PMB#417
Larkfield, OR 85374
866-392-5074 US Toll Free
123-456-3190 Cell
gpinfold@plavorix.com
The old tag line that we had on the business cars was.
Delivering Dependable Drawing and Document Tools to Design Teams Worldwide.
If you have an idea for a better tag line we are open to that also.
Updates
We would like to thank all of the Designers for their wonderful work. We apologize that we will not have the time to provide feedback to everyone. There is just so many innovative and professional designs that you have all created making our decision even harder.
Target Market(s)
Architects and Engineers
Industry/Entity Type
Business
Look and feel

```html
<!DOCTYPE html>
<html lang="en">
<head>
<meta charset="utf-8">
<title>Plavorix Business Card</title>
<link rel="stylesheet" href="https://fonts.googleapis.com/css2?family=Barlow:wght@400;500;700;800&display=swap">
<style>
  :root {
    --backdrop: #e6e4e1;
    --card: #f2f2f1;
    --ink: #5a5a5a;
    --ink-soft: #777777;
    --orange: #e2501f;
    --orange-light: #f08a2a;
    --crimson: #a8202c;
  }
  * { box-sizing: border-box; margin: 0; padding: 0; }
  html, body {
    width: 1200px; height: 900px; overflow: hidden;
    background: var(--backdrop);
    font-family: "Barlow", Arial, sans-serif;
    color: var(--ink);
  }
  .stage { position: relative; width: 1200px; height: 900px; }
  .card {
    position: absolute;
    width: 560px; height: 320px;
    background: var(--card);
    box-shadow: 0 6px 18px rgba(0,0,0,0.12);
    overflow: hidden;
  }
  .card--front { left: 320px; top: 90px; }
  .card--back { left: 320px; top: 480px; }

  /* Front */
  .brand {
    position: absolute; left: 60px; top: 100px;
    display: flex; align-items: center; gap: 14px;
  }
  .brand__dot {
    width: 58px; height: 58px; border-radius: 50%;
    background: var(--orange);
  }
  .brand__name {
    font-weight: 800; font-size: 64px; letter-spacing: -1px;
    color: var(--ink); line-height: 1;
  }
  .tagline {
    position: absolute; left: 132px; top: 190px;
    padding-left: 12px;
    border-left: 3px solid var(--orange);
    font-size: 14px; line-height: 1.35; color: var(--ink-soft);
  }

  /* Back */
  .corner-shape {
    position: absolute; right: -70px; top: -110px;
    width: 300px; height: 300px; border-radius: 50%;
    background: linear-gradient(135deg, var(--orange-light), var(--orange) 60%, var(--crimson));
  }
  .edge-tab {
    position: absolute; left: 0; top: 62px;
    width: 10px; height: 14px; background: var(--orange);
  }
  .person { position: absolute; left: 42px; top: 52px; }
  .person__name {
    font-size: 26px; font-weight: 500; letter-spacing: 1px;
    text-transform: uppercase; color: var(--ink);
  }
  .person__title { font-size: 17px; color: var(--ink-soft); margin-top: 2px; }
  .contacts {
    position: absolute; left: 42px; top: 142px;
    list-style: none; font-size: 16px; color: var(--ink-soft);
  }
  .contacts li { display: flex; align-items: flex-start; gap: 12px; margin-bottom: 9px; line-height: 1.3; }
  .contacts svg { flex: none; width: 22px; height: 22px; }
</style>
</head>
<body>
<main class="stage">

  <section class="card card--front" aria-label="Card front">
    <div class="brand">
      <span class="brand__dot"></span>
      <span class="brand__name">Plavorix</span>
    </div>
    <p class="tagline">Delivering Dependable Drawing and Document Tools<br>to Design Teams Worldwide</p>
  </section>

  <section class="card card--back" aria-label="Card back">
    <div class="corner-shape"></div>
    <span class="edge-tab"></span>
    <div class="person">
      <h1 class="person__name">Gerald Pinfold</h1>
      <p class="person__title">Vice President</p>
    </div>
    <ul class="contacts">
      <li>
        <svg viewBox="0 0 22 22" aria-hidden="true"><circle cx="11" cy="11" r="11" fill="#e2501f"/><path d="M6 9c0-2 2-3 5-3s5 1 5 3l-2 1-1-2h-4l-1 2zM7 11h8l1 4H6z" fill="#fff"/></svg>
        <span>866-392-5074 US Toll Free</span>
      </li>
      <li>
        <svg viewBox="0 0 22 22" aria-hidden="true"><circle cx="11" cy="11" r="11" fill="#e2501f"/><rect x="7.5" y="5" width="7" height="12" rx="1.2" fill="#fff"/><rect x="8.7" y="6.5" width="4.6" height="7.5" fill="#e2501f"/></svg>
        <span>123-456-3190</span>
      </li>
      <li>
        <svg viewBox="0 0 22 22" aria-hidden="true"><circle cx="11" cy="11" r="11" fill="#e2501f"/><rect x="5.5" y="7" width="11" height="8" fill="#fff"/><path d="M5.5 7l5.5 4.5L16.5 7" fill="none" stroke="#e2501f" stroke-width="1.2"/></svg>
        <span>gpinfold@plavorix.com</span>
      </li>
      <li>
        <svg viewBox="0 0 22 22" aria-hidden="true"><circle cx="11" cy="11" r="11" fill="#e2501f"/><path d="M11 4.5a4.2 4.2 0 0 1 4.2 4.2c0 3-4.2 8-4.2 8s-4.2-5-4.2-8A4.2 4.2 0 0 1 11 4.5z" fill="#fff"/><circle cx="11" cy="8.7" r="1.6" fill="#e2501f"/></svg>
        <span>4738 W. Harrowgate Lane. STE 305<br>PMB#417<br>Larkfield, OR 85374</span>
      </li>
    </ul>
  </section>

</main>
</body>
</html>
```